i need a business card for a plumbing company in california

we are a drain cleaning , maintenance plumbing company who is starting new marketing campaign for a tatrench-less pipe installation department .

Target Market(s)

the professional who appreciates time and quality workmanship.

Industry/Entity Type

Plumbing

Colors
0655a3
ec1f27

Requirements
Must have
• the second logo needs to be included
Nice to have
• a focus on the services offered
Should not have
• any underlined words on the brief

```html
<!DOCTYPE html>
<html lang="en">
<head>
<meta charset="utf-8">
<title>Harbor Flow Plumbing – Business Card</title>
<link rel="stylesheet" href="https://fonts.googleapis.com/css2?family=Arimo:wght@400;700&display=swap">
<style>
  :root {
    --stone: #7a796c;
    --red: #e0222a;
    --ink: #2b2b2b;
    --paper: #ffffff;
    --backdrop: #e9e9e6;
  }
  * { margin: 0; padding: 0; box-sizing: border-box; }
  html, body { width: 1200px; height: 782px; overflow: hidden; }
  body {
    background: var(--backdrop);
    font-family: "Arimo", Arial, sans-serif;
    color: var(--ink);
    position: relative;
  }
  .card {
    position: absolute;
    top: 236px;
    width: 540px;
    height: 309px;
    overflow: hidden;
    box-shadow: 0 6px 18px rgba(0,0,0,.18);
  }
  .card--front { left: 40px; background: var(--paper); }
  .card--back { left: 620px; background: var(--stone); }

  .front-corner { position: absolute; left: 0; top: 0; }
  .holder { position: absolute; left: 62px; top: 26px; }
  .holder__name {
    color: var(--red); font-weight: 700; font-size: 17px; letter-spacing: .3px;
    text-transform: uppercase;
  }
  .holder__title { font-size: 12px; color: #444; margin-top: 1px; }
  .holder__rule {
    position: absolute; left: 52px; top: 64px; width: 148px; height: 2px; background: var(--red);
  }

  .contacts { position: absolute; left: 24px; top: 120px; list-style: none; }
  .contacts li {
    display: flex; align-items: center; gap: 7px;
    font-size: 13px; line-height: 19px; color: #222;
  }
  .contacts svg { width: 11px; height: 11px; fill: var(--red); flex: none; }

  .brand {
    position: absolute; display: flex; align-items: center; gap: 12px;
    font-weight: 700; line-height: 1;
  }
  .card--front .brand { right: 36px; top: 128px; color: var(--stone); font-size: 30px; }
  .brand__mark { width: 22px; height: 22px; background: var(--red); flex: none; }
  .brand__name { display: block; }

  .address {
    position: absolute; right: 38px; top: 226px; text-align: right;
    font-size: 14px; line-height: 18px; color: #222;
  }
  .front-bands { position: absolute; left: 0; bottom: 0; }

  .card--back .brand {
    left: 50%; top: 50%; transform: translate(-50%, -50%);
    color: var(--paper); font-size: 34px;
  }
  .card--back .brand__mark { background: var(--paper); width: 24px; height: 24px; }
</style>
</head>
<body>
  <section class="card card--front" aria-label="Business card front">
    <svg class="front-corner" width="60" height="60" viewBox="0 0 60 60" aria-hidden="true">
      <polygon points="0,0 26,0 0,34" fill="var(--stone)"/>
      <polygon points="34,18 52,18 52,56 14,56" fill="var(--red)"/>
    </svg>
    <div class="holder">
      <p class="holder__name">Daniel Reyes</p>
      <p class="holder__title">Managing Director</p>
    </div>
    <span class="holder__rule"></span>

    <ul class="contacts">
      <li><svg viewBox="0 0 12 12"><path d="M1 2c0-.6.4-1 1-1h8c.6 0 1 .4 1 1v1.5H8.2L7.6 2.4H4.4L3.8 3.5H1zM2 5h8l1 6H1z"/></svg>055-310 428 615</li>
      <li><svg viewBox="0 0 12 12"><path d="M3.5 0h5c.6 0 1 .4 1 1v10c0 .6-.4 1-1 1h-5c-.6 0-1-.4-1-1V1c0-.6.4-1 1-1zm.5 1.5v7.5h4V1.5z"/></svg>055-310 428 615</li>
      <li><svg viewBox="0 0 12 12"><path d="M0 2h12v8H0zm1 1 5 4 5-4z" fill-rule="evenodd"/></svg>info@harborflow.com</li>
      <li><svg viewBox="0 0 12 12"><circle cx="6" cy="6" r="5.5"/><path d="M.5 6h11M6 .5c2 2.5 2 8.5 0 11M6 .5c-2 2.5-2 8.5 0 11" stroke="#fff" stroke-width=".8" fill="none"/></svg>www.harborflow.com</li>
    </ul>

    <div class="brand">
      <span class="brand__name">Harbor Flow<br>Plumbing</span>
      <span class="brand__mark"></span>
    </div>

    <address class="address" style="font-style:normal">
      2180, Marina Vista Road<br>Oakland, CA 94607
    </address>

    <svg class="front-bands" width="540" height="70" viewBox="0 0 540 70" aria-hidden="true">
      <polygon points="0,0 226,70 0,70" fill="var(--stone)"/>
      <polygon points="0,6 200,68 0,68" fill="var(--stone)" opacity="0"/>
      <polygon points="236,52 272,38 540,38 540,70 226,70" fill="var(--red)"/>
    </svg>
  </section>

  <section class="card card--back" aria-label="Business card back">
    <div class="brand">
      <span class="brand__name">Harbor Flow<br>Plumbing</span>
      <span class="brand__mark"></span>
    </div>
  </section>
</body>
</html>
```